Awesome photographers card for an awesome new business

Double sided business card Black background and silver logo in middle on one side. Details on otherside. please keep it simple

Industry/Entity Type

Photographer

Contact Information for Business Card

Gerald Fenwick
0452817360
GeraldFenwickPhotography47@mailbox.test
www.GeraldFenwickPhotography.test.au
Instagram _Gerald_fenwick

Requirements
Must have
• My logo in Silver
• please use instagram logo instead of "Instagram"

```html
<!DOCTYPE html>
<html lang="en">
<head>
<meta charset="utf-8">
<title>Gerald Fenwick Photography – Business Card</title>
<link rel="stylesheet" href="https://fonts.googleapis.com/css2?family=Montserrat:wght@400;500;700&display=swap">
<style>
  :root {
    --canvas-bg: #ededed;
    --card-white: #fbfbfb;
    --ink: #2b2b2b;
    --ink-soft: #6a6a6a;
    --accent-red: #d0202e;
    --photo-dark: #1c1c1c;
    --photo-mid: #5a5a5a;
    --photo-light: #a9a9a9;
    --silver: #f2f2f2;
  }
  * { box-sizing: border-box; margin: 0; padding: 0; }
  html, body {
    width: 1200px; height: 1200px; overflow: hidden;
    background: var(--canvas-bg);
    font-family: "Montserrat", sans-serif;
  }
  .sheet {
    width: 1200px; height: 1200px;
    display: flex; flex-direction: column;
    align-items: center; justify-content: center;
    gap: 60px;
  }
  .card {
    width: 840px; height: 480px;
    position: relative; overflow: hidden;
    box-shadow: 0 4px 18px rgba(0,0,0,0.10);
  }

  /* Front side: photo with centred logo */
  .card--front { background: var(--photo-dark); }
  .card__photo {
    position: absolute; inset: 0;
    background:
      radial-gradient(ellipse at 20% 30%, var(--photo-light) 0%, transparent 45%),
      linear-gradient(160deg, var(--photo-mid) 0%, #3a3a3a 35%, var(--photo-dark) 70%, #111 100%);
  }
  .brand-mark {
    position: absolute; left: 50%; top: 50%;
    transform: translate(-50%, -50%);
    width: 300px; height: 300px;
    display: flex; align-items: center; justify-content: center;
  }
  .brand-mark__ring {
    position: absolute; inset: 0;
    border: 4px solid var(--silver); border-radius: 50%;
  }
  .brand-mark__name {
    color: var(--silver);
    font-weight: 500; font-size: 30px;
    letter-spacing: 4px; text-transform: uppercase;
    text-align: center; line-height: 1.4;
  }

  /* Back side: contact details */
  .card--back { background: var(--card-white); }
  .details {
    position: absolute; left: 300px; top: 150px;
  }
  .details__name {
    font-weight: 700; font-size: 30px; color: var(--ink);
    text-transform: uppercase; letter-spacing: 1px;
  }
  .details__rule {
    width: 40px; height: 3px; background: var(--accent-red);
    margin: 16px 0 12px;
  }
  .details__list { list-style: none; }
  .details__item {
    font-size: 15px; color: var(--ink-soft); line-height: 1.65;
  }
  .details__label { color: var(--accent-red); font-weight: 500; margin-right: 6px; }
  .details__web {
    font-size: 17px; font-weight: 500; color: var(--accent-red);
  }
</style>
</head>
<body>
<main class="sheet">
  <section class="card card--front">
    <div class="card__photo" role="img" aria-label="Black and white street photograph of a classic car and its front wheel"></div>
    <div class="brand-mark">
      <span class="brand-mark__ring"></span>
      <span class="brand-mark__name">Gerald<br>Fenwick</span>
    </div>
  </section>

  <section class="card card--back">
    <div class="details">
      <h1 class="details__name">Gerald Fenwick</h1>
      <div class="details__rule"></div>
      <ul class="details__list">
        <li class="details__item"><span class="details__label">t |</span>045 281 7360</li>
        <li class="details__item"><span class="details__label">e |</span>GeraldFenwickPhotography47@mailbox.test</li>
        <li class="details__item"><span class="details__label">i |</span>Instagram _Gerald_fenwick</li>
      </ul>
      <div class="details__rule"></div>
      <p class="details__web">www.GeraldFenwickPhotography.test.au</p>
    </div>
  </section>
</main>
</body>
</html>
```